Velvet Lantern rebranding my business with a new business card

I have my new logo and now I need a refresher on my business cards. I really want something fun and fresh. I like black background or anything to make the color pop.
Logo
Name: Velvet Lantern
Contact Info as stated below:
Mira Pellow
555-013-4762
Logo
Name: Velvet Lantern
Mira Pellow
555-013-4762
fb.me/VelvetLanternbyMira
Instagram: @VelvetLanternbyMira

Industry/Entity Type

Business

Contact Information for Business Card

double-sided. Logo on one side. Contact info on the other.

Requirements
Must have
• Logo
• Name: Velvet Lantern
• Contact Info as stated below:
• Mira Pellow
• 555-013-4762
• fb.me/VelvetLanternbyMira
• fb.me/VelvetLanternbyMira

```html
<!DOCTYPE html>
<html lang="en">
<head>
<meta charset="utf-8">
<title>Velvet Lantern — Business Card</title>
<link href="https://fonts.googleapis.com/css2?family=Roboto:wght@400;500&family=Roboto+Condensed:wght@700&display=swap" rel="stylesheet">
<style>
  :root {
    --backdrop: #e9e6e2;
    --card-black: #1b1c1e;
    --card-white: #f4f4f4;
    --ink: #2a2a2a;
    --ink-soft: #4a4a4a;
    --rule: #bdbdbd;
    --pink: #f2b3c6;
    --pink-ring: #f0a9bd;
    --white: #ffffff;
  }
  * { margin: 0; padding: 0; box-sizing: border-box; }
  html, body { width: 1200px; height: 960px; overflow: hidden; }
  body {
    background: var(--backdrop);
    font-family: "Roboto", Arial, sans-serif;
    position: relative;
  }
  .card {
    position: absolute;
    border-radius: 22px;
    overflow: hidden;
    box-shadow: 0 6px 14px rgba(0,0,0,0.25);
  }
  .card-front {
    left: 320px; top: 100px; width: 610px; height: 355px;
    background: var(--card-black);
  }
  .front-logo {
    position: absolute; left: 0; right: 0; top: 235px;
    transform: translateY(-50%);
    text-align: center;
    font-family: "Roboto Condensed", "Arial Narrow", sans-serif;
    font-weight: 700; font-size: 40px; letter-spacing: 1px;
    color: var(--white);
  }
  .front-url {
    position: absolute; left: 0; right: 0; top: 298px;
    text-align: center;
    font-size: 14px; letter-spacing: 5px;
    color: var(--white);
  }
  .card-back {
    left: 320px; top: 492px; width: 600px; height: 344px;
    background: var(--card-white);
  }
  .back-stripe { position: absolute; left: 0; bottom: 0; width: 600px; height: 12px; }
  .logo-badge {
    position: absolute; left: 89px; top: 96px; width: 166px; height: 166px;
    border-radius: 50%; background: var(--white);
    border: 1.5px solid #222;
    display: flex; align-items: center; justify-content: center;
  }
  .logo-badge::before {
    content: ""; position: absolute; inset: 5px;
    border-radius: 50%; border: 2px solid var(--pink-ring);
  }
  .badge-name {
    font-family: "Roboto Condensed", "Arial Narrow", sans-serif;
    font-weight: 700; font-size: 22px; line-height: 1.05;
    text-align: center; color: var(--ink);
  }
  .divider {
    position: absolute; left: 280px; top: 112px; width: 1px; height: 132px;
    background: var(--rule);
  }
  .contact { position: absolute; left: 305px; top: 116px; }
  .contact-name {
    font-family: "Roboto Condensed", "Arial Narrow", sans-serif;
    font-weight: 700; font-size: 22px; color: var(--ink);
    margin-bottom: 28px;
  }
  .contact-list { list-style: none; }
  .contact-list li {
    display: flex; align-items: center; gap: 9px;
    font-size: 15px; line-height: 19.5px; color: var(--ink-soft);
  }
  .contact-list svg { width: 12px; height: 12px; flex: none; }
</style>
</head>
<body>
  <section class="card card-front" aria-label="Card front">
    <div class="front-logo">Velvet Lantern</div>
    <div class="front-url">www.velvetlantern.com</div>
  </section>

  <section class="card card-back" aria-label="Card back">
    <div class="logo-badge"><span class="badge-name">Velvet<br>Lantern</span></div>
    <div class="divider"></div>
    <div class="contact">
      <div class="contact-name">MIRA PELLOW</div>
      <ul class="contact-list">
        <li>
          <svg viewBox="0 0 12 12" aria-hidden="true"><path d="M2.4 0.8l2 2.1-1 1.4c.8 1.6 1.9 2.7 3.4 3.4l1.4-1 2.1 2-1 2.1C5.7 10.6 1.4 6.3 0.6 1.8z" fill="#2a2a2a"/></svg>
          <span>555-013-4762</span>
        </li>
        <li>
          <svg viewBox="0 0 12 12" aria-hidden="true"><circle cx="6" cy="6" r="5.2" fill="none" stroke="#2a2a2a" stroke-width="1.3"/><ellipse cx="6" cy="6" rx="2.2" ry="5.2" fill="none" stroke="#2a2a2a" stroke-width="1"/><path d="M1 6h10" stroke="#2a2a2a" stroke-width="1"/></svg>
          <span>www.velvetlantern.com</span>
        </li>
        <li>
          <svg viewBox="0 0 12 12" aria-hidden="true"><rect x="0.5" y="0.5" width="11" height="11" rx="1.5" fill="#2a2a2a"/></svg>
          <span>fb.me/VelvetLanternbyMira</span>
        </li>
      </ul>
    </div>
    <svg class="back-stripe" viewBox="0 0 600 12" preserveAspectRatio="none" aria-hidden="true">
      <polygon points="0,0 395,0 389,12 0,12" fill="#111"/>
      <polygon points="395,0 600,0 600,12 389,12" fill="#f2b3c6"/>
    </svg>
  </section>
</body>
</html>
```